New Webpage for High Class Expert Witness Services Company

We are looking for a minimalist design for a webpage that just has our logo and an entry form offer to connect with one of our Liaisons.
The entry form should just ask for Name, Email, Contact Info and Description of Project.

Company Name is: The Marlowe Crest Advisory Services

Number of Pages Required

1 page

```html
<!DOCTYPE html>
<html lang="en">
<head>
<meta charset="utf-8">
<title>Marlowe Crest Advisory Services</title>
<link href="https://fonts.googleapis.com/css2?family=Cinzel:wght@400;700&family=Roboto:wght@400&display=swap" rel="stylesheet">
<style>
  :root {
    --bg: #030303;
    --panel: rgba(18,18,18,0.72);
    --line: #5a5a5a;
    --field-line: #8a8a8a;
    --text: #f2f2f2;
    --silver: #c4c4c4;
    --muted: #a9a9a9;
    --gold-light: #f1e3a2;
    --gold-dark: #dcb95a;
    --ink: #111111;
    --phone-icon: #d8b866;
  }
  * { box-sizing: border-box; margin: 0; padding: 0; }
  html, body { width: 1200px; height: 740px; overflow: hidden; background: var(--bg); }
  .page {
    position: relative; width: 1200px; height: 740px; overflow: hidden;
    background: linear-gradient(120deg, #000 0%, #070707 45%, #111 100%);
    font-family: "Roboto", Arial, sans-serif; color: var(--text);
  }
  .mesh-backdrop {
    position: absolute; left: 400px; top: 420px; width: 800px; height: 320px;
    background: radial-gradient(ellipse at 85% 80%, rgba(150,150,150,0.22) 0%, rgba(90,90,90,0.10) 40%, rgba(0,0,0,0) 72%);
  }
  .brand {
    position: absolute; left: 139px; top: 50px; display: flex; align-items: center; gap: 12px;
    font-family: "Cinzel", Georgia, serif; font-weight: 400; color: var(--silver);
  }
  .brand-mark { width: 40px; height: 40px; background: var(--silver); }
  .brand-name { font-size: 24px; line-height: 1.1; letter-spacing: 1px; width: 320px; }
  .phone {
    position: absolute; right: 97px; top: 42px; display: flex; align-items: center; gap: 10px;
    font-family: "Cinzel", Georgia, serif; font-size: 26px; color: var(--text);
  }
  .phone svg { width: 26px; height: 26px; }
  .hero { position: absolute; left: 139px; top: 220px; color: var(--silver); font-family: "Cinzel", Georgia, serif; }
  .hero-kicker { font-size: 15.5px; letter-spacing: 2.2px; color: var(--muted); }
  .hero-title { margin-top: 14px; font-size: 57px; font-weight: 400; line-height: 58px; }
  .liaison-form {
    position: absolute; left: 687px; top: 120px; width: 417px; height: 448px;
    border: 1px solid var(--line); background: var(--panel);
  }
  .form-title {
    position: absolute; left: 0; right: 0; top: 38px; text-align: center;
    font-family: "Cinzel", Georgia, serif; font-weight: 400; font-size: 24.5px; letter-spacing: 0.3px;
  }
  .field {
    position: absolute; left: 50px; width: 329px; height: 42px;
    border: 1px solid var(--field-line); background: rgba(0,0,0,0.35);
    padding: 12px 17px; font-size: 13px; color: var(--text);
  }
  .field-name { top: 89px; }
  .field-email { top: 147px; }
  .field-phone { top: 201px; }
  .field-project { top: 257px; height: 88px; }
  .submit {
    position: absolute; left: 50px; top: 358px; width: 332px; height: 44px;
    background: linear-gradient(100deg, var(--gold-light) 0%, var(--gold-light) 45%, var(--gold-dark) 85%);
    color: var(--ink); font-family: "Cinzel", Georgia, serif; font-weight: 700; font-size: 15px;
    letter-spacing: 0.5px; display: flex; align-items: center; justify-content: center;
  }
  .footer-rule { position: absolute; left: 0; right: 0; top: 678px; border-top: 1px solid #3a3a3a; }
  .footer-note { position: absolute; left: 0; right: 0; top: 699px; text-align: center; font-size: 12.5px; color: var(--muted); }
</style>
</head>
<body>
<div class="page">
  <div class="mesh-backdrop" role="img" aria-label="Faint silver wireframe mesh texture"></div>

  <header>
    <div class="brand">
      <span class="brand-mark"></span>
      <span class="brand-name">Marlowe Crest Advisory Services</span>
    </div>
    <div class="phone">
      <svg viewBox="0 0 24 24" fill="none" stroke="var(--phone-icon)" stroke-width="1.4" stroke-linejoin="round">
        <path d="M5 3h4l1.6 4.5-2.4 1.6a12 12 0 0 0 6.7 6.7l1.6-2.4L21 15v4a2 2 0 0 1-2 2A17 17 0 0 1 3 5a2 2 0 0 1 2-2z"/>
      </svg>
      <span>800-555-0142</span>
    </div>
  </header>

  <section class="hero">
    <p class="hero-kicker">MARLOWE CREST ADVISORY SERVICES</p>
    <h1 class="hero-title">SEAMLESS<br>MEDICAL EXPERT<br>INTEGRATION</h1>
  </section>

  <form class="liaison-form">
    <h2 class="form-title">CONNECT WITH A LIAISON</h2>
    <div class="field field-name">Name*</div>
    <div class="field field-email">Email*</div>
    <div class="field field-phone">Phone number*</div>
    <div class="field field-project">Description of Project</div>
    <div class="submit">SUBMIT</div>
  </form>

  <div class="footer-rule"></div>
  <p class="footer-note">© 2026 Marlowe Crest Advisory Services. All Rights Reserved</p>
</div>
</body>
</html>
```